Corvane Business Cards

Front of business card will have logo, name, address, & telephone number. Back of card will have a list of services provided - Roads, Substation Pads, Temporary Pads, Site Pads, Land Leveling, Powerline Row Cleaning, Land Clearing, Gates, Fencing, Construction Entrances, Excavation, Trenching, Underground Utilities, Directional Boring, Pile Driving. We are a construction company that uses heavy equipment like bulldozers, motor graders/blades, dump trucks, backhoes, hydro axes, & skid loaders. We build roads, pads, & install electric utility lines & waterlines underground. This logo is new. The word "Construction" can be smaller as uploaded 2 example edited logos. We will be using this card design for many employees.
Target Market(s)
Industrial Electric Powerline, Wind Turbine, Solar Panel, & Water Utility companies.
Contact Information for Business Card
Name/Position - Dwayne Halster - Owner
Address: 4875 FM 309
Dunmore Flats, NM 87412
Phone number - (505) 482-5096

```html
<!DOCTYPE html>
<html lang="en">
<head>
<meta charset="utf-8">
<title>Corvane Business Cards</title>
<link href="https://fonts.googleapis.com/css2?family=Arimo:wght@400;700&display=swap" rel="stylesheet">
<style>
  :root {
    --backdrop: #cfcfcf;
    --card-maroon: #3a1119;
    --card-white: #f6f6f6;
    --ink-maroon: #3a1119;
    --ink-dark: #2b2b2b;
    --rule: #b9a3a7;
  }
  * { margin: 0; padding: 0; box-sizing: border-box; }
  html, body {
    width: 1200px;
    height: 802px;
    overflow: hidden;
    background: var(--backdrop);
    font-family: "Arimo", Arial, sans-serif;
  }
  .canvas { position: relative; width: 1200px; height: 802px; }
  .card {
    position: absolute;
    top: 274px;
    width: 443px;
    height: 265px;
    background: var(--card-maroon);
    overflow: hidden;
  }
  .card--front { left: 136px; }
  .card--back { left: 608px; }

  .front-field {
    position: absolute;
    left: 34px;
    top: 0;
    width: 332px;
    height: 265px;
    background: var(--card-white);
  }
  .contact {
    position: absolute;
    left: 131px;
    top: 75px;
    color: var(--ink-dark);
    white-space: nowrap;
  }
  .contact__name {
    font-weight: 700;
    font-size: 15px;
    color: var(--ink-maroon);
    letter-spacing: 0.2px;
  }
  .contact__role {
    font-size: 12px;
    margin-top: 2px;
    letter-spacing: 0.3px;
  }
  .contact__rule {
    width: 91px;
    height: 1px;
    background: var(--rule);
    margin: 8px 0 6px;
  }
  .contact__phone { font-size: 16px; }
  .contact__address { font-size: 13px; line-height: 18px; }

  .brand {
    position: absolute;
    left: 0;
    right: 0;
    top: 96px;
    text-align: center;
    color: var(--card-white);
    font-weight: 700;
    text-transform: uppercase;
    white-space: nowrap;
  }
  .brand__name {
    font-size: 44px;
    letter-spacing: 1px;
    line-height: 48px;
  }
  .brand__sub {
    font-size: 24px;
    letter-spacing: 0.5px;
    line-height: 28px;
    margin-top: 40px;
  }
</style>
</head>
<body>
<main class="canvas">
  <section class="card card--front" aria-label="Business card front">
    <div class="front-field"></div>
    <div class="contact">
      <p class="contact__name">DWAYNE HALSTER</p>
      <p class="contact__role">OWNER</p>
      <div class="contact__rule"></div>
      <p class="contact__phone">(505) 482-5096</p>
      <div class="contact__rule"></div>
      <p class="contact__address">4875 FM 309<br>Dunmore Flats, NM 87412</p>
    </div>
  </section>

  <section class="card card--back" aria-label="Business card back">
    <div class="brand">
      <p class="brand__name">Corvane</p>
      <p class="brand__sub">Construction</p>
    </div>
  </section>
</main>
</body>
</html>
```